Heron Property Inspection business card

I am the principal inspector of Heron Property Inspections. I serve Northern Virginia from Winchester to Arlington.Associate, Federated Guild of Dwelling Examiners (FGDE)Graduate, FGDE Home Inspectors CourseNational Association of Home Inspectors ExamI'd like the business card to look more professional than comical.I pulled the attached picture off the web. I'd like to have something like that or an image of a house as my logo on the cards.

Target Market(s)

Persons who recently purchased a home.

Industry/Entity Type

Business

Contact Information for Business Card

Bob AllenBadger Home Inspections, LLC.4455 River RoadBluemont, Virginia 20135cell: 703-231-6680e-mail: tkmarlow@postvale.net

Font styles to use
Serif
Sans Serif

Requirements
Must have
• I'd like to have a logo, something that identifies me as a home inspector. The attached images are something that I'd like to have incorporated into my business card logo.
Nice to have
• I'd like a sketch of a house and/or a magnifying glass showing a house being inspected. The attached images are used as a suggestion only, I do not own the images.
Should not have
• Gimmicky stuff. I want to appear professional and trustworthy.

```html
<!DOCTYPE html>
<html lang="en">
<head>
<meta charset="utf-8">
<title>Heron Property Inspection – Business Card</title>
<link rel="stylesheet" href="https://fonts.googleapis.com/css2?family=PT+Sans:wght@400;700&family=Crimson+Text:wght@400;600&display=swap">
<style>
  :root {
    --page-bg: #e9e6e0;
    --card-white: #ffffff;
    --green-light: #8cc84b;
    --green-mid: #4fb04a;
    --green-deep: #1f9a5a;
    --green-dark: #0d7a3c;
    --ink: #1b1b1b;
    --arc-line: #111111;
    --icon-green: #5cb85c;
  }
  * { box-sizing: border-box; margin: 0; padding: 0; }
  html, body {
    width: 1200px;
    height: 818px;
    overflow: hidden;
    background: var(--page-bg);
  }
  .stage {
    width: 1200px;
    height: 818px;
    display: flex;
    align-items: center;
    justify-content: center;
  }
  .card {
    position: relative;
    width: 700px;
    height: 400px;
    overflow: hidden;
    background: var(--card-white);
    box-shadow: 0 10px 30px rgba(0,0,0,0.18);
  }
  .card-backdrop {
    position: absolute;
    inset: 0;
  }
  .identity {
    position: absolute;
    left: 48px;
    top: 52px;
  }
  .identity .person {
    font-family: "PT Sans", sans-serif;
    font-weight: 700;
    font-size: 38px;
    color: var(--ink);
    letter-spacing: 0.5px;
  }
  .identity .company-row {
    display: flex;
    align-items: center;
    gap: 12px;
    margin-top: 8px;
    padding-top: 8px;
    border-top: 3px solid var(--green-mid);
  }
  .identity .company-mark {
    width: 18px;
    height: 18px;
    background: var(--green-mid);
  }
  .identity .company {
    font-family: "PT Sans", sans-serif;
    font-weight: 400;
    font-size: 28px;
    color: var(--ink);
  }
  .address {
    position: absolute;
    left: 300px;
    top: 196px;
    font-family: "Crimson Text", serif;
    font-size: 19px;
    line-height: 1.25;
    color: var(--ink);
  }
  .contact {
    position: absolute;
    left: 48px;
    top: 268px;
    list-style: none;
    font-family: "Crimson Text", serif;
    font-size: 19px;
    color: var(--ink);
  }
  .contact li {
    display: flex;
    align-items: center;
    gap: 12px;
    margin-bottom: 8px;
  }
  .contact svg { width: 22px; height: 20px; flex: none; }
  .role {
    position: absolute;
    right: 34px;
    bottom: 30px;
    font-family: "Crimson Text", serif;
    font-size: 26px;
    color: var(--card-white);
    letter-spacing: 0.5px;
  }
</style>
</head>
<body>
<main class="stage">
  <article class="card">
    <svg class="card-backdrop" width="700" height="400" viewBox="0 0 700 400" aria-hidden="true">
      <defs>
        <linearGradient id="greenField" x1="0" y1="1" x2="1" y2="0">
          <stop offset="0" stop-color="#0f8a4a"/>
          <stop offset="0.45" stop-color="#3fae52"/>
          <stop offset="1" stop-color="#9ccf55"/>
        </linearGradient>
      </defs>
      <rect width="700" height="400" fill="url(#greenField)"/>
      <ellipse cx="120" cy="120" rx="480" ry="318" fill="#ffffff" stroke="#111111" stroke-width="4"/>
    </svg>

    <header class="identity">
      <div class="person">Tim Marlow</div>
      <div class="company-row">
        <span class="company-mark"></span>
        <span class="company">Heron Property Inspections, LLC</span>
      </div>
    </header>

    <address class="address" style="font-style:normal">
      7182 Quarry Lane<br>Fernhill, Virginia 20148
    </address>

    <ul class="contact">
      <li>
        <svg viewBox="0 0 22 20" aria-hidden="true">
          <rect x="0" y="0" width="22" height="20" rx="2" fill="var(--icon-green)"/>
          <rect x="7" y="3" width="8" height="14" rx="1.5" fill="none" stroke="#fff" stroke-width="1.6"/>
          <circle cx="11" cy="14.5" r="1" fill="#fff"/>
        </svg>
        <span>703-555-0192</span>
      </li>
      <li>
        <svg viewBox="0 0 22 20" aria-hidden="true">
          <rect x="0" y="0" width="22" height="20" rx="2" fill="var(--icon-green)"/>
          <rect x="4" y="5" width="14" height="10" fill="none" stroke="#fff" stroke-width="1.6"/>
          <polyline points="4,5 11,11 18,5" fill="none" stroke="#fff" stroke-width="1.6"/>
        </svg>
        <span>tkmarlow@postvale.net</span>
      </li>
    </ul>

    <div class="role">Employee Name</div>
  </article>
</main>
</body>
</html>
```